VORLAND COMPOSITES INC website in USA

VORLAND COMPOSITES INC incorporated and operated in USA needs a completely new design of website. This Wyoming based company is a importer and distributor of composites material to supply mainly to American and Canadian/Mexican customers. Our main products includes Carbon Fiber, Aramid Fiber, Glass Fiber, Basalt Fiber, High Silica Glass, Quartz Fiber, S-Glass, Alumina Fiber, Vacuum Auxiliary.

We are one stop composites solution provider for Automotive, Aerospace, Construction, Electrical and Machinery industries.

We are exclusive sales company in North America for BLORAN composites produced from China and their other Asia facilities.

Target Market(s)

USA and Canada

Industry/Entity Type

Composites materials

Coding

Coded - Design and coding required

Number of Pages Required

5+ page

Requirements
Nice to have
• Color theme to match our corporate logo VORLAND. VORLAND stands for Northgate Provisioning Trade Holdings

```html
<!DOCTYPE html>
<html lang="en">
<head>
<meta charset="utf-8">
<title>VORLAND COMPOSITES INC</title>
<link href="https://fonts.googleapis.com/css2?family=Roboto:ital,wght@0,400;0,500;0,700;1,500;1,700&display=swap" rel="stylesheet">
<style>
:root{
  --orange:#f39322;
  --ink:#2b2b2b;
  --muted:#6b6b6b;
  --light:#f4f4f4;
  --field:#e8e8e8;
  --black:#0b0b0b;
  --white:#ffffff;
}
*{box-sizing:border-box;margin:0;padding:0}
html,body{width:1200px;height:4252px;overflow:hidden}
body{position:relative;font-family:'Roboto',sans-serif;color:var(--ink);background:var(--white)}
.abs{position:absolute}
.btn{position:absolute;display:flex;align-items:center;justify-content:center;background:var(--orange);color:var(--white);font-weight:700;font-size:17px;border-radius:24px;text-transform:uppercase;letter-spacing:.2px}
.eyebrow{font-size:31px;font-weight:500;color:var(--orange);text-transform:uppercase;letter-spacing:.5px}
.eyebrow sup{font-size:18px;margin-left:8px}
.rule{height:4px;background:linear-gradient(90deg,var(--ink) 0 50%,var(--orange) 50%)}
.heading{font-size:35px;font-weight:700;color:var(--ink)}

/* header */
.topbar{left:627px;top:0;width:573px;height:37px;background:var(--orange);clip-path:polygon(0 0,100% 0,100% 100%,40px 100%);color:#fff;font-size:18px;display:flex;align-items:center;gap:28px;padding-left:56px}
.brand{left:112px;top:20px;display:flex;align-items:center;gap:16px}
.brand-name{font-size:38px;font-weight:700;color:var(--orange);letter-spacing:1px}
.brand-tag{font-size:11px;line-height:14px;color:var(--ink);border-left:2px solid var(--ink);padding-left:12px;width:120px}
.nav{left:441px;top:67px;display:flex;gap:30px;font-size:15px;font-weight:500}
.nav .on{color:var(--orange)}
.nav-contact{left:957px;top:54px;width:132px;height:44px}

/* hero */
.hero{left:0;top:114px;width:1200px;height:650px}
.hero-title{left:113px;top:200px;font-size:40px;line-height:52px;color:#fff;font-weight:500;text-transform:uppercase}
.hero-title span{color:var(--orange);font-weight:400}
.hero-copy{left:113px;top:366px;width:460px;font-size:16px;line-height:26px;color:#eee}
.hero-note{left:114px;top:532px;font-size:17px;line-height:26px;color:#fff;font-style:italic;font-weight:500}
.dots{left:567px;top:655px;display:flex;gap:7px}
.dots i{width:11px;height:11px;border-radius:50%;background:#fff}
.dots i:first-child{background:var(--orange)}

/* about */
.about-copy{left:628px;top:1020px;width:460px;font-size:15px;line-height:26px;color:var(--muted)}

/* products */
.products{left:0;top:1353px;width:1200px;height:586px;background:var(--light)}
.card{position:absolute;top:1569px;width:231px;height:289px;background:#fff;border-radius:8px;overflow:hidden;box-shadow:0 2px 8px rgba(0,0,0,.08)}
.card .ph{height:236px}
.card .lbl{display:flex;justify-content:space-between;align-items:center;padding:0 14px;height:53px;font-size:17px;font-weight:500}

/* partnership */
.partner{left:0;top:1939px;width:1200px;height:587px}
.partner-copy{left:160px;top:2149px;width:880px;text-align:center;font-size:15px;line-height:26px;color:#fff}

/* industries */
.ind{position:absolute;display:flex;align-items:center;gap:14px;font-size:21px;font-weight:500;color:#444}
.ind .badge{width:48px;height:48px;border-radius:50%;background:var(--orange);display:flex;align-items:center;justify-content:center}

/* contact */
.contact{left:0;top:3218px;width:1200px;height:600px;background:var(--light)}
.field{position:absolute;background:var(--field);border-radius:3px;font-size:13px;color:#555;padding:22px 10px 0}
.info{position:absolute;left:110px;display:flex;gap:24px}
.info .ic{width:60px;height:60px;border-radius:50%;background:var(--orange);display:flex;align-items:center;justify-content:center}
.info b{display:block;font-size:17px;color:var(--ink);margin-top:-4px}
.info p{font-size:14px;line-height:21px;color:var(--muted)}

/* footer */
.footnav{left:0;top:4014px;width:1200px;text-align:center;font-size:18px;font-weight:500;color:#fff;word-spacing:4px}
.social{left:462px;top:4076px;display:flex;gap:10px}
.social span{width:47px;height:47px;border-radius:50%;border:2px solid #fff;display:flex;align-items:center;justify-content:center;font-size:11px;font-weight:500;color:#fff}
.social span:first-child{border-color:var(--orange);color:var(--orange)}
.copy{left:0;top:4183px;width:1200px;text-align:center;font-size:17px;color:#fff}
</style>
</head>
<body>

<!-- header -->
<div class="abs topbar"><span>&#9993; hello@vorland-mail.com</span><span>|</span><span>&#9990; +1 555-010-2040</span></div>
<div class="abs brand">
  <div class="brand-name">VORLAND</div>
  <div class="brand-tag">Northgate Provisioning Trade Holdings</div>
</div>
<nav class="abs nav"><span class="on">HOME</span><span>ABOUT US</span><span>PRODUCTS</span><span>INDUSTRIES</span><span>SOLUTIONS</span></nav>
<div class="btn nav-contact">Contact</div>

<!-- hero -->
<svg class="abs hero" viewBox="0 0 1200 650">
  <defs>
    <linearGradient id="heroFill" x1="0" x2="1" y1="0" y2="0.4">
      <stop offset="0" stop-color="#050505"/><stop offset=".4" stop-color="#15181b"/><stop offset=".7" stop-color="#4e5861"/><stop offset="1" stop-color="#b4bcc2"/>
    </linearGradient>
  </defs>
  <polygon points="0,0 1200,0 1200,506 600,645 0,506" fill="var(--orange)"/>
  <polygon points="0,0 1200,0 1200,496 600,628 0,496" fill="url(#heroFill)" role="img" aria-label="Photo of a woven carbon fiber sheet in a factory"/>
</svg>
<h1 class="abs hero-title"><span>Advanced Composite</span><br>Materials for Tomorrow’s<br>Engineering</h1>
<p class="abs hero-copy">Reliable sourcing, superior quality, and complete composite solutions for the automotive, aerospace, construction, electrical, and machinery industries.</p>
<div class="btn" style="left:113px;top:471px;width:217px;height:42px">Request a Quote</div>
<p class="abs hero-note">Trusted distributor of high-performance<br>composites across North America.</p>
<div class="abs dots"><i></i><i></i><i></i><i></i></div>

<!-- about -->
<svg class="abs" style="left:104px;top:818px" width="470" height="458">
  <defs>
    <linearGradient id="aboutPhoto" x1="0" y1="0" x2="1" y2="1">
      <stop offset="0" stop-color="#e0711c"/><stop offset=".35" stop-color="#b9561a"/><stop offset=".55" stop-color="#3e7f9c"/><stop offset=".8" stop-color="#2a2d31"/><stop offset="1" stop-color="#121314"/>
    </linearGradient>
  </defs>
  <circle cx="232" cy="228" r="230" fill="var(--orange)"/>
  <circle cx="240" cy="222" r="222" fill="url(#aboutPhoto)" role="img" aria-label="Photo of gloved hands cutting carbon fiber fabric"/>
</svg>
<div class="abs eyebrow" style="left:628px;top:840px">About<sup>*</sup></div>
<div class="abs rule" style="left:628px;top:886px;width:44px;background:var(--ink)"></div>
<h2 class="abs heading" style="left:628px;top:914px;line-height:43px">Our Trusted Partner<br>in Composite Innovation</h2>
<p class="abs about-copy">VORLAND COMPOSITES INC. is a Wyoming-based importer and distributor of advanced composite materials, serving customers across the United States, Canada, and Mexico. We provide a complete range of high-performance fibers and materials, ensuring exceptional strength, durability, and reliability for critical engineering applications.</p>
<div class="btn" style="left:628px;top:1200px;width:217px;height:42px">Request a Quote</div>

<!-- products -->
<div class="abs products"></div>
<div class="abs eyebrow" style="left:520px;top:1418px">Products<sup>*</sup></div>
<div class="abs rule" style="left:509px;top:1466px;width:182px"></div>
<h2 class="abs heading" style="left:0;width:1200px;text-align:center;top:1494px">Product Categories</h2>
<svg class="abs" style="left:66px;top:1685px" width="20" height="34"><path d="M16 2 2 17l14 15" stroke="#111" stroke-width="3" fill="none"/></svg>
<svg class="abs" style="left:1110px;top:1685px" width="20" height="34"><path d="M4 2l14 15L4 32" stroke="#111" stroke-width="3" fill="none"/></svg>
<div class="card" style="left:111px"><div class="ph" style="background:linear-gradient(160deg,#8a96a3,#1e2226)" role="img" aria-label="Photo of carbon fiber rolls"></div><div class="lbl">Carbon Fiber<svg width="28" height="28"><circle cx="14" cy="14" r="12" stroke="#222" stroke-width="1.6" fill="none"/><path d="M8 14h12m-5-5 5 5-5 5" stroke="#222" stroke-width="1.6" fill="none"/></svg></div></div>
<div class="card" style="left:360px"><div class="ph" style="background:linear-gradient(100deg,#2a2a2a,#6b6b3a,#d8c23a)" role="img" aria-label="Photo of aramid fiber braided sleeves"></div><div class="lbl">Aramid Fiber<svg width="28" height="28"><circle cx="14" cy="14" r="12" stroke="var(--orange)" stroke-width="1.6" fill="none"/><path d="M8 14h12m-5-5 5 5-5 5" stroke="var(--orange)" stroke-width="1.6" fill="none"/></svg></div></div>
<div class="card" style="left:608px"><div class="ph" style="background:linear-gradient(160deg,#aab6c0,#c4692a,#7d8790)" role="img" aria-label="Photo of glass fiber cables"></div><div class="lbl">Glass Fiber<svg width="28" height="28"><circle cx="14" cy="14" r="12" stroke="#222" stroke-width="1.6" fill="none"/><path d="M8 14h12m-5-5 5 5-5 5" stroke="#222" stroke-width="1.6" fill="none"/></svg></div></div>
<div class="card" style="left:857px"><div class="ph" style="background:linear-gradient(160deg,#c9c9c9,#5c5c5c)" role="img" aria-label="Photo of basalt fiber tubes"></div><div class="lbl">Basalt Fiber<svg width="28" height="28"><circle cx="14" cy="14" r="12" stroke="#222" stroke-width="1.6" fill="none"/><path d="M8 14h12m-5-5 5 5-5 5" stroke="#222" stroke-width="1.6" fill="none"/></svg></div></div>

<!-- partnership -->
<svg class="abs partner" viewBox="0 0 1200 587">
  <defs><linearGradient id="pt" x1="0" y1="0" x2="1" y2="1"><stop offset="0" stop-color="#2f2824"/><stop offset=".5" stop-color="#4a3f38"/><stop offset="1" stop-color="#2c2521"/></linearGradient></defs>
  <polygon points="0,0 1200,0 1200,438 600,587 0,438" fill="url(#pt)"/>
</svg>
<div class="abs eyebrow" style="left:496px;top:1996px">Partnership<sup>*</sup></div>
<h2 class="abs" style="left:0;width:1200px;text-align:center;top:2080px;font-size:35px;font-weight:700;color:#fff">Our Partnership with <span style="color:var(--orange)">BLORAN Composites</span></h2>
<p class="abs partner-copy">As the exclusive North American sales company for BLORAN Composites, VORLAND offers direct access to globally recognized products manufactured in China and other Asian facilities. This partnership ensures competitive pricing, consistent quality, and reliable supply for all our clients in the Americas.</p>
<div class="abs" style="left:390px;top:2255px;width:395px;height:68px;background:var(--orange);clip-path:polygon(8% 0,100% 0,92% 100%,0 100%);color:#fff;font-style:italic;font-weight:700;font-size:19px;line-height:26px;text-align:center;padding-top:8px">Global Production, Local Support<br>The Best of Both Worlds.</div>
<div class="abs" style="left:387px;top:2368px;width:427px;height:43px;border:1.5px solid var(--orange);border-radius:22px;color:#fff;font-weight:700;font-size:17px;display:flex;align-items:center;justify-content:center">LEARN MORE ABOUT BLORAN PARTNERSHIP</div>

<!-- industries -->
<div class="abs eyebrow" style="left:119px;top:2622px">Industries<sup>*</sup></div>
<div class="abs rule" style="left:119px;top:2668px;width:92px"></div>
<h2 class="abs heading" style="left:119px;top:2698px">Industries We Serve</h2>
<div class="ind" style="left:119px;top:2774px"><span class="badge"><svg width="28" height="20" viewBox="0 0 28 20"><path d="M3 12l3-6c1-2 2-3 4-3h8c2 0 3 1 4 3l3 6v4H3z" fill="none" stroke="#fff" stroke-width="2" stroke-linejoin="round"/><circle cx="8" cy="16" r="2.5" fill="#fff"/><circle cx="20" cy="16" r="2.5" fill="#fff"/></svg></span>Automotive</div>
<div class="ind" style="left:333px;top:2774px"><span class="badge"><svg width="26" height="26" viewBox="0 0 26 26"><path d="M13 2c1 0 2 1 2 3v6l9 5v2l-9-2v5l3 2v2l-5-1-5 1v-2l3-2v-5l-9 2v-2l9-5V5c0-2 1-3 2-3z" fill="#fff"/></svg></span>Aerospace</div>
<div class="ind" style="left:119px;top:2861px"><span class="badge"><svg width="28" height="22" viewBox="0 0 28 22"><path d="M5 16a9 9 0 0 1 18 0z" fill="#fff"/><rect x="2" y="16" width="24" height="3" rx="1.5" fill="#fff"/><rect x="12" y="4" width="4" height="6" fill="var(--orange)"/></svg></span>Construction</div>
<div class="ind" style="left:333px;top:2861px"><span class="badge"><svg width="20" height="28" viewBox="0 0 20 28"><path d="M12 1 2 16h7l-2 11L18 11h-7z" fill="#fff"/></svg></span>Electrical</div>
<div class="ind" style="left:119px;top:2945px"><span class="badge"><svg width="28" height="28" viewBox="0 0 28 28"><g stroke="#fff" stroke-width="4" stroke-linecap="round"><path d="M14 3v4M14 21v4M3 14h4M21 14h4M6 6l3 3M19 19l3 3M22 6l-3 3M9 19l-3 3"/></g><circle cx="14" cy="14" r="7" fill="#fff"/><circle cx="14" cy="14" r="3" fill="var(--orange)"/></svg></span>Machinery</div>
<div class="btn" style="left:119px;top:3033px;width:366px;height:43px">Discover Industry Applications</div>
<svg class="abs" style="left:628px;top:2602px" width="495" height="490">
  <defs>
    <linearGradient id="indPhoto" x1="0" y1="0" x2="0.3" y2="1">
      <stop offset="0" stop-color="#8b8f92"/><stop offset=".35" stop-color="#55595d"/><stop offset=".65" stop-color="#24272a"/><stop offset="1" stop-color="#9a9ca0"/>
    </linearGradient>
  </defs>
  <circle cx="245" cy="243" r="244" fill="var(--orange)"/>
  <circle cx="253" cy="238" r="237" fill="url(#indPhoto)" role="img" aria-label="Photo of a carbon fiber car body in a workshop"/>
</svg>

<!-- contact -->
<div class="abs contact"></div>
<div class="abs eyebrow" style="left:528px;top:3282px">Contact<sup>*</sup></div>
<div class="abs rule" style="left:509px;top:3328px;width:182px"></div>
<h2 class="abs heading" style="left:0;width:1200px;text-align:center;top:3356px">Get In Touch</h2>
<div class="info" style="top:3453px"><div class="ic"><svg width="20" height="26"><path d="M10 1a8 8 0 0 1 8 8c0 6-8 16-8 16S2 15 2 9a8 8 0 0 1 8-8z" fill="#fff"/><circle cx="10" cy="9" r="3" fill="var(--orange)"/></svg></div><div><b>Address</b><p>VORLAND COMPOSITES INC.<br>Registered Office: Wyoming, USA</p></div></div>
<div class="info" style="top:3553px"><div class="ic"><svg width="24" height="18"><rect width="24" height="18" rx="2" fill="#fff"/><path d="M1 2l11 8 11-8" stroke="var(--orange)" stroke-width="2" fill="none"/></svg></div><div><b>Email</b><p>hello@vorlandcomposites-mail.com</p></div></div>
<div class="info" style="top:3656px"><div class="ic"><svg width="22" height="22"><path d="M5 1l4 5-2 3c1 3 3 5 6 6l3-2 5 4-3 4C9 21 1 13 1 4z" fill="#fff"/></svg></div><div><b>Phone</b><p>+1 - 555-010-2040</p></div></div>
<div class="field" style="left:477px;top:3455px;width:274px;height:54px">First Name</div>
<div class="field" style="left:477px;top:3521px;width:274px;height:54px">Last Name</div>
<div class="field" style="left:477px;top:3587px;width:274px;height:54px">Phone</div>
<div class="field" style="left:477px;top:3655px;width:274px;height:54px">Email</div>
<div class="field" style="left:771px;top:3455px;width:316px;height:188px">Message</div>
<div class="btn" style="left:771px;top:3663px;width:316px;height:43px">Send Now</div>

<!-- footer -->
<svg class="abs" style="left:0;top:3772px" width="1200" height="480">
  <polygon points="0,120 590,4 1200,120 1200,480 0,480" fill="var(--orange)"/>
  <polygon points="0,116 590,16 1200,116 1200,480 0,480" fill="var(--black)"/>
</svg>
<div class="abs" style="left:440px;top:3910px;display:flex;align-items:center;gap:16px">
  <div class="brand-name" style="color:#fff">VORLAND</div>
  <div class="brand-tag" style="color:#fff;border-color:#fff">Northgate Provisioning Trade Holdings</div>
</div>
<div class="abs footnav">HOME | ABOUT | PRODUCTS | INDUSTRIES | PARTNERSHIP | CONTACT</div>
<div class="abs social"><span>Kivo</span><span>Orbl</span><span>Zelo</span><span>Mavi</span><span>Tixa</span></div>
<div class="abs copy">© 2025 VORLAND COMPOSITES INC. All Rights Reserved.</div>

</body>
</html>
```